High-End Print/Digital Ad for Unique Luxury Travel Company Required

Objective:
Design a compelling and visually striking advertisement that highlights our company’s unmatched luxury travel experiences. The ad should elevate our brand image, spark curiosity, and drive prospective clients to contact us.
Target Audience:
• Affluent individuals seeking extraordinary, tailor-made travel experiences
• Affluent, luxury, high-net-worth individuals looking for value, expertise, and white-glove service
• Professionals or retirees who appreciate unique, thoughtfully curated travel over mainstream tourism
Key Messages to Communicate:
• One-of-a-kind luxury travel: Once-in-a-lifetime experiences that are curated with creativity and meticulous attention to detail
• Exceptional service: White-glove, personalized planning from start to finish
• 38 years’ travel experience – expert knowledge of destinations, modes of travel, premium accommodations and well-established, meaningful industry connections.
• Highly trusted: Cruise line executives often say, “No one does what you do.”
Tone and Style:
• Elegant, luxurious, sophisticated
• Eye-catching, polished, and modern
• Professional but warm—conveys trust and credibility
• High-impact visuals (full-bleed imagery, custom graphics, or high-end photography)
Deliverables:
• One full-page print ad and digital ad
• Ready-to-print, high-resolution file + working file (PSD, AI, etc.)
Optional: Social media-optimized version or short motion-graphic variation (if designer offers it)
Inspiration & Visual Style Suggestions:
• Think Lumen Voyages, Harrow Pike Wanderer, Silver Quill, or Orvel Retreats ad styles
• Large, emotive imagery with elegant typography
• Clean layout that speaks luxury, clarity, and trust
Copy Direction (draft):
For those who’ve explored the world—and crave something beyond the ordinary.
Each journey is a masterfully curated experience, rich in detail, seamless in execution, and unforgettable in every way.
Founded in 1997, Tidewell Journeys is a unique travel company specializing in cruising, all-inclusive luxury properties, and tours world-wide for individuals, groups, and incentives.
We offer an exceptional range of services designed to ensure every journey is flawlessly executed and truly unforgettable.
Let us help you plan your next extraordinary adventure.
Note: You may refine the copy slightly based on layout or format needs.
Other Resources for References:
1. Website - www.tidewelljourneys-example.com

```html
<!DOCTYPE html>
<html lang="en">
<head>
<meta charset="utf-8">
<title>Tidewell Journeys – Luxury Travel Flyer</title>
<link href="https://fonts.googleapis.com/css2?family=Inter:wght@400;500;600;700;800&display=swap" rel="stylesheet">
<style>
  :root {
    --navy: #0b4a8b;
    --navy-deep: #0a427d;
    --ink: #1e2430;
    --paper: #ffffff;
    --backdrop: #d6d7d9;
  }
  * { margin: 0; padding: 0; box-sizing: border-box; }
  html, body { width: 903px; height: 1200px; overflow: hidden; }
  body {
    background: var(--backdrop);
    font-family: "Inter", Arial, sans-serif;
    color: var(--ink);
    position: relative;
  }
  .flyer {
    position: absolute;
    left: 41px; top: 20px;
    width: 820px; height: 1160px;
    background: var(--paper);
    overflow: hidden;
  }
  .corner { position: absolute; top: 0; }
  .corner-left { left: 0; }
  .corner-right { right: 0; }

  .brand {
    position: absolute;
    left: 0; right: 0; top: 46px;
    display: flex; align-items: center; justify-content: center;
    gap: 14px;
  }
  .brand-dot {
    width: 60px; height: 60px; border-radius: 50%;
    background: var(--navy);
  }
  .brand-name {
    font-size: 44px; font-weight: 600; color: var(--navy);
    letter-spacing: 0.5px;
  }

  .collage {
    position: absolute; left: 0; top: 169.5px;
    width: 820px; height: 569px;
  }

  .service-label {
    position: absolute;
    text-align: center;
    color: var(--navy);
    font-weight: 600;
    font-size: 19px;
    line-height: 25px;
  }
  .service-individual { left: 347px; top: 662px; width: 120px; }
  .service-group { left: 634px; top: 652px; width: 120px; }
  .mark-dot {
    position: absolute; left: 96px; top: 643px;
    width: 56px; height: 56px; border-radius: 50%;
    background: var(--navy);
  }

  .welcome {
    position: absolute; left: 40px; top: 714px;
    color: var(--navy); font-weight: 600; font-size: 22px;
  }
  .headline {
    position: absolute; left: 39px; top: 752px; width: 390px;
    color: var(--navy); font-weight: 800; font-size: 30px; line-height: 35px;
  }
  .intro {
    position: absolute; left: 40px; width: 360px;
    font-size: 16.4px; line-height: 24.8px; font-weight: 400;
  }
  .intro-1 { top: 874px; }
  .intro-2 { top: 1016px; }

  .divider {
    position: absolute; left: 425px; top: 765px;
    width: 2px; height: 290px; background: var(--navy);
  }
  .about {
    position: absolute; left: 465px; width: 320px;
    font-size: 16.4px; line-height: 24.8px;
  }
  .about-1 { top: 800px; }
  .about-2 { top: 954px; }

  .call-box {
    position: absolute; left: 423px; top: 1055px;
    width: 397px; height: 105px;
    background: var(--navy-deep);
    color: #fff;
  }
  .call-icon { position: absolute; left: 31px; top: 33px; }
  .call-label {
    position: absolute; left: 96px; top: 18px;
    font-size: 19px; font-weight: 400;
  }
  .call-number {
    position: absolute; left: 95px; top: 44px;
    font-size: 31px; font-weight: 800; letter-spacing: 0.5px;
  }
  .base-band {
    position: absolute; left: 0; bottom: 0;
    width: 820px; height: 12px; background: var(--navy-deep);
  }
</style>
</head>
<body>
  <main class="flyer">
    <svg class="corner corner-left" width="98" height="71" viewBox="0 0 98 71" aria-hidden="true"><polygon points="0,0 98,0 0,71" fill="var(--navy)"/></svg>
    <svg class="corner corner-right" width="86" height="62" viewBox="0 0 86 62" aria-hidden="true"><polygon points="0,0 86,0 86,62" fill="var(--navy)"/></svg>

    <header class="brand">
      <span class="brand-dot"></span>
      <span class="brand-name">Tidewell Journeys</span>
    </header>

    <svg class="collage" viewBox="0 267 1292 896" preserveAspectRatio="none">
      <defs>
        <linearGradient id="g-tower" x1="0" y1="0" x2="0" y2="1"><stop offset="0" stop-color="#5f86b8"/><stop offset="1" stop-color="#9a8f82"/></linearGradient>
        <linearGradient id="g-sunsea" x1="0" y1="0" x2="0" y2="1"><stop offset="0" stop-color="#d89c66"/><stop offset="1" stop-color="#6f8c8c"/></linearGradient>
        <linearGradient id="g-palace" x1="0" y1="0" x2="1" y2="1"><stop offset="0" stop-color="#c98a7a"/><stop offset="1" stop-color="#a85b48"/></linearGradient>
        <linearGradient id="g-canal" x1="0" y1="0" x2="0" y2="1"><stop offset="0" stop-color="#4b6f9a"/><stop offset="1" stop-color="#2f5c86"/></linearGradient>
        <linearGradient id="g-harbour" x1="0" y1="0" x2="0" y2="1"><stop offset="0" stop-color="#3c7fc4"/><stop offset="0.55" stop-color="#c0714a"/><stop offset="1" stop-color="#2f6b80"/></linearGradient>
        <linearGradient id="g-meadow" x1="0" y1="0" x2="0" y2="1"><stop offset="0" stop-color="#7ea2d0"/><stop offset="0.5" stop-color="#4f8a3c"/><stop offset="1" stop-color="#b0548c"/></linearGradient>
        <linearGradient id="g-cliff" x1="0" y1="0" x2="1" y2="1"><stop offset="0" stop-color="#a79270"/><stop offset="1" stop-color="#6b7a4c"/></linearGradient>
        <linearGradient id="g-desert" x1="0" y1="0" x2="1" y2="1"><stop offset="0" stop-color="#f2c466"/><stop offset="1" stop-color="#a87e56"/></linearGradient>
        <linearGradient id="g-abbey" x1="0" y1="0" x2="0" y2="1"><stop offset="0" stop-color="#5b93d6"/><stop offset="0.5" stop-color="#d2b048"/><stop offset="1" stop-color="#4c7a3a"/></linearGradient>
        <linearGradient id="g-lagoon" x1="0" y1="0" x2="0" y2="1"><stop offset="0" stop-color="#d4e4ee"/><stop offset="1" stop-color="#3fb4bd"/></linearGradient>
        <linearGradient id="g-skyline" x1="0" y1="0" x2="0" y2="1"><stop offset="0" stop-color="#9fb8d6"/><stop offset="1" stop-color="#3e6694"/></linearGradient>
        <linearGradient id="g-village" x1="0" y1="0" x2="0" y2="1"><stop offset="0" stop-color="#3f6aa6"/><stop offset="0.55" stop-color="#c0a472"/><stop offset="1" stop-color="#7d8a92"/></linearGradient>
        <linearGradient id="g-arch" x1="0" y1="0" x2="0" y2="1"><stop offset="0" stop-color="#8e7f86"/><stop offset="0.6" stop-color="#d4896a"/><stop offset="1" stop-color="#4a4646"/></linearGradient>
        <linearGradient id="g-waterpark" x1="0" y1="0" x2="0" y2="1"><stop offset="0" stop-color="#62b0d8"/><stop offset="1" stop-color="#2f9ad0"/></linearGradient>
      </defs>
      <polygon role="img" aria-label="Photo: stone medieval tower under blue sky" fill="url(#g-tower)" points="194,56 413,275 194,494 -25,275"/>
      <polygon role="img" aria-label="Photo: rocky coastline at sunset" fill="url(#g-sunsea)" points="644,56 863,275 644,494 425,275"/>
      <polygon role="img" aria-label="Photo: ornate palace and onion-domed cathedral" fill="url(#g-palace)" points="1094,56 1313,275 1094,494 875,275"/>
      <polygon role="img" aria-label="Photo: grand canal with gondolas at dusk" fill="url(#g-canal)" points="-31,278 188,497 -31,716 -250,497"/>
      <polygon role="img" aria-label="Photo: walled old town with red roofs by the sea" fill="url(#g-harbour)" points="419,278 638,497 419,716 200,497"/>
      <polygon role="img" aria-label="Photo: wildflower meadow below snowy mountains" fill="url(#g-meadow)" points="869,278 1088,497 869,716 650,497"/>
      <polygon role="img" aria-label="Photo: cliffside villas over the sea" fill="url(#g-cliff)" points="1319,278 1538,497 1319,716 1100,497"/>
      <polygon role="img" aria-label="Photo: pyramid and resting camel at sunrise" fill="url(#g-desert)" points="194,500 413,719 194,938 -25,719"/>
      <polygon role="img" aria-label="Photo: baroque abbey on a green hill above a river" fill="url(#g-abbey)" points="644,500 863,719 644,938 425,719"/>
      <polygon role="img" aria-label="Photo: overwater bungalows in a turquoise lagoon" fill="url(#g-lagoon)" points="1094,500 1313,719 1094,938 875,719"/>
      <polygon role="img" aria-label="Photo: modern city skyline by the water" fill="url(#g-skyline)" points="-31,722 188,941 -31,1160 -250,941"/>
      <polygon role="img" aria-label="Photo: seaside village church and bell tower" fill="url(#g-village)" points="419,722 638,941 419,1160 200,941"/>
      <polygon role="img" aria-label="Photo: sea rock arch at sunset" fill="url(#g-arch)" points="869,722 1088,941 869,1160 650,941"/>
      <polygon role="img" aria-label="Photo: resort water park with slides" fill="url(#g-waterpark)" points="1319,722 1538,941 1319,1160 1100,941"/>
    </svg>

    <span class="mark-dot" aria-hidden="true"></span>
    <p class="service-label service-individual">Individual<br>TRAVEL</p>
    <p class="service-label service-group">Group<br>TRAVEL</p>

    <p class="welcome">Welcome to</p>
    <h1 class="headline">TIDEWELL JOURNEYS<br>A Luxury Travel<br>COMPANY</h1>

    <p class="intro intro-1">For those who’ve explored the world - and crave something beyond the ordinary. Each journey is a masterfully curated experience, rich in detail, seamless in execution, and unforgettable in every way</p>
    <p class="intro intro-2">We offer an exceptional range of services designed to ensure every journey is flawlessly executed and truly unforgettable.</p>

    <span class="divider" aria-hidden="true"></span>

    <p class="about about-1">Founded in 1997, Tidewell Journeys is a unique travel company specializing in cruising, all-inclusive luxury properties, and tours world -wide for individuals, groups, and incentives.</p>
    <p class="about about-2">Let us help you plan your next extraordinary adventure,</p>

    <section class="call-box">
      <svg class="call-icon" width="40" height="40" viewBox="0 0 40 40" aria-hidden="true">
        <circle cx="20" cy="20" r="18.5" fill="none" stroke="#fff" stroke-width="2"/>
        <path d="M14.5 11.5 l3 0 l1.6 4.6 l-2.2 1.6 c1.2 2.6 3 4.4 5.6 5.6 l1.6-2.2 l4.6 1.6 l0 3 c0 1.2-1 2-2.2 1.9 c-7.4-0.6-12.9-6.1-13.5-13.5 c-0.1-1.2 0.7-2.6 1.5-2.6 z" fill="none" stroke="#fff" stroke-width="1.8" stroke-linejoin="round"/>
      </svg>
      <p class="call-label">Call Us</p>
      <p class="call-number">1-800-555-0147</p>
    </section>
    <span class="base-band" aria-hidden="true"></span>
  </main>
</body>
</html>
```